Business Card for Coastal Tundrabridge Advisory

We need a business card for Coastal Tundrabridge Advisory. The company website address is provided below. The company logo is attached. We provide specialized permafrost services to the mining, transportation, and oil & gas industries. The card should be prepared for:
Matthias Korhonen, PhD.
Coastal Tundrabridge Advisory
PO Box 418259
Quillwater, Alaska 99642
Direct: +1-907-555-0143
Email: mkorhonen@tundrabridgeadvisory.example
Website: www.coastaltundrabridgeadvisory.example

```html
<!DOCTYPE html>
<html lang="en">
<head>
<meta charset="utf-8">
<title>Coastal Tundrabridge Advisory – Business Card</title>
<link href="https://fonts.googleapis.com/css2?family=Montserrat:wght@400;600;700&display=swap" rel="stylesheet">
<style>
  :root {
    --backdrop: #9b9b9b;
    --card-light: #ffffff;
    --ink: #111820;
    --ink-soft: #1c232b;
    --paper-text: #ffffff;
  }
  * { box-sizing: border-box; margin: 0; padding: 0; }
  html, body {
    width: 1093px; height: 1200px; overflow: hidden;
    background: var(--backdrop);
    font-family: "Montserrat", Arial, sans-serif;
  }
  .canvas { position: relative; width: 1093px; height: 1200px; }

  .card {
    position: absolute; left: 264px; width: 581px; height: 348px;
    border-radius: 16px; overflow: hidden;
  }
  .card--front { top: 225px; background: var(--card-light); color: var(--ink); }
  .card--back { top: 616px; height: 366px; background: var(--ink); color: var(--paper-text); }

  .wordmark {
    position: absolute; text-align: center; font-weight: 600;
    text-transform: uppercase; line-height: 1.2;
  }
  .card--front .wordmark {
    left: 56px; width: 176px; top: 189px;
    font-size: 11.5px; letter-spacing: 1.4px;
  }
  .card--back .wordmark {
    left: 0; right: 0; top: 146px;
    font-size: 28px; letter-spacing: 4px;
  }

  .divider {
    position: absolute; left: 242px; top: 121px; width: 1.5px; height: 167px;
    background: var(--ink);
  }

  .details { position: absolute; left: 251px; top: 120px; }
  .person-name { font-size: 18px; font-weight: 700; line-height: 22px; }
  .person-title { font-size: 12.5px; line-height: 18px; margin-top: 1px; }
  .address { font-size: 12.5px; line-height: 16.5px; margin-top: 10px; padding-left: 2px; }

  .contacts { list-style: none; margin-top: 16px; padding-left: 2px; }
  .contact {
    display: flex; align-items: center; height: 25.5px;
    font-size: 12px; white-space: nowrap;
  }
  .contact svg { width: 13px; height: 13px; margin-right: 10px; flex: none; fill: var(--ink-soft); }
</style>
</head>
<body>
<main class="canvas">

  <section class="card card--front" aria-label="Card front">
    <div class="wordmark">Coastal Tundrabridge<br>Advisory</div>
    <div class="divider"></div>
    <div class="details">
      <p class="person-name">Matthias Korhonen, PhD.</p>
      <p class="person-title">Managing Director</p>
      <p class="address">PO Box 418259<br>Quillwater, Alaska 99642</p>
      <ul class="contacts">
        <li class="contact">
          <svg viewBox="0 0 24 24" aria-hidden="true"><path d="M6.6 10.8c1.4 2.8 3.8 5.1 6.6 6.6l2.2-2.2c.3-.3.7-.4 1-.2 1.1.4 2.3.6 3.6.6.6 0 1 .4 1 1V20c0 .6-.4 1-1 1C10.6 21 3 13.4 3 4c0-.6.4-1 1-1h3.5c.6 0 1 .4 1 1 0 1.3.2 2.5.6 3.6.1.3 0 .7-.2 1z"/></svg>
          +1-907-555-0143
        </li>
        <li class="contact">
          <svg viewBox="0 0 24 24" aria-hidden="true"><path d="M3 5h18v14H3z M3 6l9 6 9-6" fill="var(--ink-soft)"/><path d="M3 6.5l9 6 9-6" fill="none" stroke="#fff" stroke-width="1.6"/></svg>
          mkorhonen@tundrabridgeadvisory.example
        </li>
        <li class="contact">
          <svg viewBox="0 0 24 24" aria-hidden="true"><circle cx="12" cy="12" r="10"/><path d="M8 6c2 1 1 3 3 3s1 3-1 3-3 1-3 3M15 14c1-1 3-1 3 1s-1 3-3 4" fill="none" stroke="#fff" stroke-width="1.5"/></svg>
          www.coastaltundrabridgeadvisory.example
        </li>
      </ul>
    </div>
  </section>

  <section class="card card--back" aria-label="Card back">
    <div class="wordmark">Coastal Tundrabridge<br>Advisory</div>
  </section>

</main>
</body>
</html>
```